Printing Company needs Website

PLEASE REVIEW ALL IMAGES, I HAVE INCLUDED A WEBSITE MOCKUP IDEA AND LOGO FILES IN THESE IMAGES.

Vel-Marks Provides printing services to multiple businesses. We Focus on 4 main markets. Signage (Signs, Banners, Wraps, Custom graphics), Printing (flyers, brochures, business cards, Postcards), Apparel (printed shirts, hoodies, sweatshirts), Promotional Products (mugs, golf balls, brava cans, pens), We try to sell ourselves on total brand imaging, our slogan is "Mark Everything." because we want to be able to provide any type of printing to our customers. Consumer targeting should be targeted towards small business, and wholesale targeting should be geared toward, merchandising, branding, marketing, design, signage, apparel, embroidery, and printing groups. WE DO OFFER DESIGN SERVICES, I have attached one orlwick guild logo design as an example.

I need a website designed both for wholesale and consumer based people. Wholesale customers would have their own login and consumers would also have their own.
I need there to be an online designer software (possibly java) built in so that the customer can order their product or upload their artwork online to see the proof for approval. There will need to be an commence setup, and I do have a quillpay account if that helps. Shipping must be auto calculated at the time of ordering. I would Like to make it to where when customer orders a product if it is outside of the dimensions requested on the site that the customer is warned of clipping or skewing.

I will be working closely aside the designer I pick to aid in the uploading and configuration of pricing structure, weight, and imagery if selected. This will be a lengthy project, and I will be willing to pay for the additional help so long as you are completely aware of the needs, Happy designing!!
Updates

I love all of the designs so far everyone! I will be reviewing PLEASE NOTE, IF I APPROVE YOUR WEB DESIGN, I WILL WANT YOU TO COMPLETE THE ENTIRE DESIGN INCLUDING A DESIGN PROOFING SETUP FOR MY CUSTOMERS INTEGRATED IN AS I HAVE STATED IN THE ORIGINAL STATEMENT. PLEASE ASK QUESTIONS IF YOU DON'T UNDERSTAND!

Target Market(s)

Small Business, School Athletics, Merchandising groups, Branding Groups, Larger Printers, Sign makers, Embroidery shops, Screen Printing Shops

Industry/Entity Type

It Company

Font styles to use
Sans Serif

Colors
000000
1b1b1b
757575
ec1f27

Requirements
Must have
• Built in design setup to each product with sizing, Ability to add pre-designed templates, .pdf print ready files after upload, Wholesale account, or Business accounts all with different pricing structures, Must be willing to aid in setup of all products and services (willing pay additional for setup costs.)
Nice to have
• SEO Optimization, targeting specific groups listed, automatic ordering to outsource vendors straight from site listing drop ship location if need be.

```html
<!DOCTYPE html>
<html lang="en">
<head>
<meta charset="utf-8">
<title>Vel-Marks — Mark Everything.</title>
<link href="https://fonts.googleapis.com/css2?family=Montserrat:wght@400;500;600;700;800&display=swap" rel="stylesheet">
<style>
  :root {
    --black: #000000;
    --ink: #1b1b1b;
    --grey: #757575;
    --red: #ec1f27;
    --white: #ffffff;
    --rule: #bdbdbd;
    --sky: #4f72b8;
    --sky-light: #86a6dc;
    --stone: #b7b2a6;
    --pavement: #9c9a94;
    --panel-blue: #2e4a7a;
    --brick: #7a4a3c;
    --wood: #9a7355;
    --lawn: #4f8a2a;
  }
  * { margin: 0; padding: 0; box-sizing: border-box; }
  html, body { width: 737px; height: 1200px; overflow: hidden; background: var(--white); }
  body { font-family: "Montserrat", Arial, sans-serif; color: var(--ink); position: relative; }

  /* Hero */
  .hero { position: absolute; left: 0; top: 0; width: 737px; height: 382px; overflow: hidden; }
  .hero-photo {
    position: absolute; inset: 0;
    background:
      radial-gradient(ellipse 90px 200px at 600px 200px, rgba(40,66,112,.95), rgba(40,66,112,0) 100%),
      radial-gradient(ellipse 60px 110px at 598px 170px, rgba(235,232,222,.9), rgba(235,232,222,0) 100%),
      radial-gradient(ellipse 220px 70px at 300px 200px, rgba(214,206,188,.85), rgba(214,206,188,0) 100%),
      radial-gradient(ellipse 180px 60px at 120px 150px, rgba(120,72,58,.7), rgba(120,72,58,0) 100%),
      radial-gradient(ellipse 160px 60px at 120px 320px, rgba(70,98,52,.7), rgba(70,98,52,0) 100%),
      linear-gradient(180deg, #3f63a8 0%, #5a80c4 22%, #88a3cf 36%, #a9a596 48%, #8f8c84 62%, #b9b7b0 78%, #a3a19a 100%);
  }
  .hero-shade { position: absolute; inset: 0; background: linear-gradient(180deg, rgba(20,30,60,.35), rgba(0,0,0,0) 28%, rgba(0,0,0,0) 70%, rgba(0,0,0,.12)); }
  .brand { position: absolute; display: flex; align-items: center; gap: 6px; }
  .brand-dot { width: 16px; height: 16px; border-radius: 50%; background: var(--red); }
  .brand-name { font-weight: 800; font-size: 20px; color: var(--white); letter-spacing: .5px; }
  .brand-tag { position: absolute; font-size: 7px; color: var(--white); font-weight: 500; }
  .hero .brand { left: 80px; top: 24px; }
  .hero .brand-tag { left: 138px; top: 49px; }

  .phone { position: absolute; left: 479px; top: 10px; display: flex; align-items: center; gap: 8px; color: var(--white); font-size: 11px; }
  .phone-ring { width: 19px; height: 19px; border: 1.2px solid var(--white); border-radius: 50%; display: flex; align-items: center; justify-content: center; }
  .search { position: absolute; left: 597px; top: 10px; width: 58px; height: 18px; border: 1px solid var(--white); color: var(--white); font-size: 5.5px; font-weight: 600; display: flex; align-items: center; padding-left: 6px; gap: 4px; }

  .nav { position: absolute; top: 40px; left: 0; width: 737px; height: 18px; }
  .nav a { position: absolute; top: 0; height: 18px; line-height: 18px; font-size: 6.8px; font-weight: 700; color: var(--white); text-decoration: none; transform: translateX(-50%); white-space: nowrap; }
  .nav a.active { background: var(--red); padding: 0 6px; }

  .hero-title { position: absolute; top: 299px; left: 0; width: 737px; text-align: center; color: var(--white); font-size: 21px; font-weight: 800; letter-spacing: 4px; text-shadow: 0 1px 3px rgba(0,0,0,.35); }
  .dots { position: absolute; top: 351px; left: 336px; display: flex; gap: 9px; align-items: center; }
  .dots span { width: 5px; height: 5px; border-radius: 50%; background: var(--white); }
  .dots span.on { width: 8px; height: 8px; background: transparent; border: 1.2px solid var(--white); }

  /* Services */
  .section-title { position: absolute; top: 407px; left: 0; width: 737px; text-align: center; color: var(--red); font-size: 16px; font-weight: 700; }
  .section-rule { position: absolute; top: 436px; left: 341px; width: 56px; height: 2px; background: var(--rule); }

  .card { position: absolute; width: 192px; height: 216px; border: 1px solid #dcdcdc; padding: 3px; background: var(--white); }
  .card-photo { position: relative; width: 100%; height: 100%; overflow: hidden; }
  .card-label { position: absolute; left: 50%; top: 50%; transform: translate(-50%, -50%); border: 1.5px solid var(--white); color: var(--white); font-weight: 700; font-size: 11px; padding: 5px 6px; white-space: nowrap; text-shadow: 0 1px 2px rgba(0,0,0,.3); }

  .card-signage .card-photo {
    background:
      radial-gradient(ellipse 60px 110px at 92px 100px, rgba(130,40,44,.55), rgba(130,40,44,0) 100%),
      radial-gradient(ellipse 40px 60px at 190px 90px, rgba(140,50,52,.45), rgba(140,50,52,0) 100%),
      linear-gradient(180deg, #c0505e 0%, #c85a60 45%, #d85a5a 75%, #e06464 100%);
  }
  .card-signage .card-label { background: var(--red); top: 102px; font-size: 11.5px; padding: 6px 10px; }
  .card-signage ul { position: absolute; top: 131px; left: 50%; transform: translateX(-50%); list-style: none; width: 70px; text-align: center; }
  .card-signage li { color: var(--white); font-size: 6.3px; font-weight: 600; line-height: 14.5px; border-bottom: 1px solid rgba(255,255,255,.6); }
  .card-signage li:last-child { border-bottom: none; width: 90px; margin-left: -10px; }

  .card-printing .card-photo {
    background:
      radial-gradient(ellipse 80px 50px at 92px 70px, rgba(70,74,80,.8), rgba(70,74,80,0) 100%),
      radial-gradient(ellipse 90px 70px at 92px 165px, rgba(215,210,196,.9), rgba(215,210,196,0) 100%),
      linear-gradient(90deg, #5e3a2e 0%, #8a6a5c 20%, #b4aca0 50%, #8a6a5c 80%, #5e3a2e 100%);
  }
  .card-printing .card-label { top: 102px; }

  .card-promo .card-photo {
    background:
      radial-gradient(ellipse 40px 40px at 40px 190px, rgba(170,60,30,.55), rgba(170,60,30,0) 100%),
      radial-gradient(ellipse 70px 110px at 100px 100px, rgba(140,100,72,.9), rgba(140,100,72,0) 100%),
      linear-gradient(90deg, #ecebe6 0%, #d8d4cc 18%, #a47e5f 34%, #8c6a50 70%, #c9c6bd 88%, #111 92%, #111 100%);
  }
  .card-promo .card-label { top: 102px; }

  .card-apparel .card-photo {
    background:
      radial-gradient(ellipse 80px 22px at 60px 104px, rgba(60,60,70,.55), rgba(60,60,70,0) 100%),
      linear-gradient(180deg, #3f7ad6 0%, #6f9ee0 30%, #e3ddcc 38%, #cfc9b8 48%, #6e7076 60%, #8a8a86 66%, #4f8a2a 72%, #5c9432 100%);
  }
  .card-apparel .card-label { top: 104px; }

  /* Footer */
  .footer { position: absolute; left: 0; top: 966px; width: 737px; height: 234px; background: var(--black); color: var(--white); }
  .footer .brand { left: 80px; top: 73px; }
  .footer .brand-tag { left: 138px; top: 98px; }
  .contact-head { position: absolute; left: 258px; top: 31px; font-size: 6.8px; font-weight: 700; }
  .contact-row { position: absolute; left: 258px; display: flex; align-items: center; gap: 13px; font-size: 6.8px; line-height: 13px; }
  .contact-icon { width: 22px; height: 22px; border: 1px solid var(--white); border-radius: 50%; display: flex; align-items: center; justify-content: center; flex-shrink: 0; }
  .map {
    position: absolute; left: 415px; top: 31px; width: 240px; height: 123px;
    background:
      radial-gradient(ellipse 50px 30px at 90px 50px, rgba(180,214,160,.9), rgba(180,214,160,0) 100%),
      radial-gradient(ellipse 60px 25px at 190px 35px, rgba(246,206,120,.7), rgba(246,206,120,0) 100%),
      linear-gradient(135deg, #e8e6e1, #dfe2da 45%, #e7e3da);
  }
  .footer-rule { position: absolute; left: 80px; top: 186px; width: 575px; height: 1px; background: #333; }
  .footer-links { position: absolute; left: 81px; top: 203px; font-size: 6px; color: var(--white); }
  .footer-links span.sep { margin: 0 4px; }
  .copyright { position: absolute; right: 82px; top: 203px; font-size: 6px; color: var(--white); }
</style>
</head>
<body>

<header class="hero">
  <div class="hero-photo" role="img" aria-label="Photo of a town street with printed historic display panels on standing doors"></div>
  <div class="hero-shade"></div>
  <div class="brand"><span class="brand-dot"></span><span class="brand-name">VEL-MARKS</span></div>
  <div class="brand-tag">Mark Everything.</div>

  <div class="phone">
    <span class="phone-ring">
      <svg width="9" height="9" viewBox="0 0 24 24"><path fill="#fff" d="M6.6 10.8a15.1 15.1 0 0 0 6.6 6.6l2.2-2.2c.3-.3.7-.4 1-.2 1.1.4 2.3.6 3.6.6.6 0 1 .4 1 1V20c0 .6-.4 1-1 1A17 17 0 0 1 3 4c0-.6.4-1 1-1h3.5c.6 0 1 .4 1 1 0 1.3.2 2.5.6 3.6.1.3 0 .7-.2 1z"/></svg>
    </span>
    <span>(555).410.2274</span>
  </div>
  <div class="search">
    <svg width="6" height="6" viewBox="0 0 12 12"><circle cx="5" cy="5" r="3.5" fill="none" stroke="#fff" stroke-width="1.5"/><path d="M7.6 7.6l3 3" stroke="#fff" stroke-width="1.5"/></svg>
    SEARCH
  </div>

  <nav class="nav">
    <a class="active" style="left:256px">HOME</a>
    <a style="left:302px">SIGNAGE</a>
    <a style="left:354px">PRINTING</a>
    <a style="left:405px">DESIGN</a>
    <a style="left:467px">PROMOTIONAL</a>
    <a style="left:524px">APPAREL</a>
    <a style="left:577px">ABOUT US</a>
    <a style="left:634px">CONTACT US</a>
  </nav>

  <h1 class="hero-title">MARK EVERYTHING</h1>
  <div class="dots"><span></span><span class="on"></span><span></span><span></span><span></span></div>
</header>

<h2 class="section-title">OUR SERVICES</h2>
<div class="section-rule"></div>

<div class="card card-signage" style="left:162px; top:465px">
  <div class="card-photo" role="img" aria-label="Brick sign pillar on a street corner with red overlay">
    <div class="card-label">SIGNAGE</div>
    <ul><li>Signs</li><li>Banners</li><li>Wraps</li><li>Custom graphics</li></ul>
  </div>
</div>

<div class="card card-printing" style="left:382px; top:465px">
  <div class="card-photo" role="img" aria-label="Printed historic plaque mounted on a brick wall">
    <div class="card-label">PRINTING</div>
  </div>
</div>

<div class="card card-promo" style="left:162px; top:716px">
  <div class="card-photo" role="img" aria-label="Engraved wooden plaque with seasonal decorations">
    <div class="card-label">PROMOTIONAL</div>
  </div>
</div>

<div class="card card-apparel" style="left:382px; top:716px">
  <div class="card-photo" role="img" aria-label="Storefront with large window graphics and lawn">
    <div class="card-label">APPAREL</div>
  </div>
</div>

<footer class="footer">
  <div class="brand"><span class="brand-dot"></span><span class="brand-name">VEL-MARKS</span></div>
  <div class="brand-tag">Mark Everything.</div>

  <div class="contact-head">CONTACT US</div>
  <div class="contact-row" style="top:48px">
    <span class="contact-icon">
      <svg width="8" height="9" viewBox="0 0 24 24"><path fill="#fff" d="M12 2a7 7 0 0 0-7 7c0 5 7 13 7 13s7-8 7-13a7 7 0 0 0-7-7zm0 9.5A2.5 2.5 0 1 1 12 6.5a2.5 2.5 0 0 1 0 5z"/></svg>
    </span>
    <span>218 Tallow Lane<br>Brinmore, OH 45117</span>
  </div>
  <div class="contact-row" style="top:90px">
    <span class="contact-icon">
      <svg width="8" height="8" viewBox="0 0 24 24"><path fill="#fff" d="M6.6 10.8a15.1 15.1 0 0 0 6.6 6.6l2.2-2.2c.3-.3.7-.4 1-.2 1.1.4 2.3.6 3.6.6.6 0 1 .4 1 1V20c0 .6-.4 1-1 1A17 17 0 0 1 3 4c0-.6.4-1 1-1h3.5c.6 0 1 .4 1 1 0 1.3.2 2.5.6 3.6.1.3 0 .7-.2 1z"/></svg>
    </span>
    <span>(555).410.2274</span>
  </div>
  <div class="contact-row" style="top:120px">
    <span class="contact-icon">
      <svg width="8" height="7" viewBox="0 0 24 18"><path fill="#fff" d="M0 0h24v18H0z"/><path d="M1 1l11 9 11-9" fill="none" stroke="#000" stroke-width="2"/></svg>
    </span>
    <span>info@velmarks.com</span>
  </div>

  <div class="map" role="img" aria-label="Street map showing the shop location"></div>

  <div class="footer-rule"></div>
  <div class="footer-links">Home<span class="sep">|</span>Signage<span class="sep">|</span>Printing<span class="sep">|</span>Design<span class="sep">|</span>promotional<span class="sep">|</span>Apparel<span class="sep">|</span>Contact Us</div>
  <div class="copyright">Copyrihts @ 2016 All Rights Reserved</div>
</footer>

</body>
</html>
```